Lifecoach needs website design based on a standard Wordpress theme

I need a website for my new lifecoaching business that can be easily implemented in Wordpress, it needs to be compatible with a standard Wordpress theme. So I can place the pictures, texts etc. in a standard theme of Wordpress.

I want the design to be a very good feeling and playfull one, based on my logo.

Target Market(s)

I will coach people to reach their goals and dreams in life.

Industry/Entity Type

Business

Requirements
Must have
• Can be easy implemented in Wordpress.
Nice to have
• Photo's of nature are nice.

```html
<!DOCTYPE html>
<html lang="en">
<head>
<meta charset="utf-8">
<title>Lena van Dorst Lifecoach</title>
<link rel="stylesheet" href="https://fonts.googleapis.com/css2?family=Open+Sans:wght@400;600&family=Arimo:wght@400;700&display=swap">
<style>
:root{
  --navy:#0c5a86;
  --sky:#19b6e8;
  --sky-deep:#0a6f9e;
  --text:#222;
  --rule:#d9d9d9;
  --footer:#555555;
  --footer-text:#f2f2f2;
  --topbar:#222;
}
*{margin:0;padding:0;box-sizing:border-box}
html,body{width:1200px;height:1068px;overflow:hidden;background:#fff}
body{position:relative;font-family:'Arimo',Arial,sans-serif;color:var(--text)}
.topbar{position:absolute;top:0;left:0;width:1200px;height:6px;background:var(--topbar)}
.brand{position:absolute;left:142px;top:45px;display:flex;align-items:center;gap:12px}
.brand-mark{width:74px;height:74px;border-radius:50%;border:4px solid var(--sky)}
.brand-name{font-family:'Open Sans',sans-serif;font-weight:400;font-size:24px;line-height:28px;color:var(--navy);letter-spacing:.5px}
.callout{position:absolute;right:145px;top:28px;text-align:center;font-family:'Open Sans',sans-serif;font-weight:600}
.callout-label{font-size:21px;color:var(--navy);line-height:28px}
.callout-phone{font-size:21px;color:var(--sky);letter-spacing:1px;line-height:28px}
.search{position:absolute;left:823px;top:99px;width:235px;height:32px;border:1px solid #ddd;border-radius:4px;background:#f4f4f4;overflow:hidden}
.search-btn{position:absolute;right:0;top:0;width:33px;height:30px;background:var(--navy)}
.nav{position:absolute;left:0;top:159px;width:1200px;height:50px;background:linear-gradient(#1fc0ee,var(--sky-deep))}
.nav ul{list-style:none;display:flex;justify-content:space-between;width:912px;margin-left:145px}
.nav li{font-family:'Open Sans',sans-serif;font-weight:600;font-size:14.5px;color:#fff;line-height:50px}
.hero{position:absolute;left:0;top:209px;width:1200px;height:408px;background:linear-gradient(180deg,#4f86d6 0%,#9cc3ee 30%,#2ea6d3 42%,#dfe8f1 58%,#f4f6f8 100%)}
.hero-dots{position:absolute;left:546px;top:367px;display:flex;gap:9px}
.hero-dots span{width:11px;height:11px;border-radius:50%;background:#888;border:2px solid #eee}
.hero-dots span.active{background:#1a6fc4}
.section-title{font-family:'Open Sans',sans-serif;font-weight:600;font-size:19.5px;color:var(--navy);padding-bottom:8px;border-bottom:1px solid var(--rule)}
.welcome{position:absolute;left:143px;top:648px;width:432px}
.welcome p{font-size:11.3px;line-height:17px;text-align:justify;margin-top:16px}
.welcome p:first-of-type{margin-top:12px}
.news{position:absolute;left:627px;top:644px;width:431px}
.news .section-title{display:flex;justify-content:space-between;align-items:center}
.news-item{display:flex;gap:13px;padding:16px 0 12px;border-bottom:1px solid var(--rule);height:85px}
.news-item:first-of-type{padding-top:14px;height:87px}
.news-thumb{flex:none;width:58px;height:58px}
.thumb-globe{background:linear-gradient(#5d9ed6,#8ccf5a)}
.thumb-island{background:linear-gradient(#6bb7e6,#37b5c4)}
.thumb-leaf{background:linear-gradient(#9fd35a,#4c8b2c)}
.news-text{font-size:11.3px;line-height:17px;text-align:justify}
.news-date{font-weight:700;font-size:11.3px;color:#1a8fc9;margin:8px 0 0 3px}
.footer{position:absolute;left:0;top:972px;width:1200px;height:96px;background:var(--footer)}
.footer-links{position:absolute;left:142px;top:19px;font-family:'Open Sans',sans-serif;font-size:14px;color:var(--footer-text)}
.footer-links span{margin:0 6px}
.copyright{position:absolute;left:142px;top:54px;font-family:'Open Sans',sans-serif;font-size:12px;letter-spacing:.8px;color:var(--footer-text)}
.social{position:absolute;left:957px;top:31px;display:flex;gap:6px}
.social span{width:21px;height:21px;border-radius:50%}
.social .s1{background:#3b5a9a}.social .s2{background:#2cb5e8}.social .s3{background:#dd4b39}.social .s4{background:#f57d00}
</style>
</head>
<body>
<div class="topbar"></div>

<header>
  <div class="brand">
    <div class="brand-mark"></div>
    <div class="brand-name">Lena van Dorst<br>Lifecoach</div>
  </div>
  <div class="callout">
    <div class="callout-label">Call for a&nbsp; life coaching:</div>
    <div class="callout-phone">1111 1111 111</div>
  </div>
  <div class="search">
    <div class="search-btn">
      <svg width="33" height="30" viewBox="0 0 33 30"><circle cx="14" cy="12" r="4" fill="none" stroke="#fff" stroke-width="2"/><line x1="17" y1="15" x2="22" y2="19" stroke="#fff" stroke-width="2.5" stroke-linecap="round"/></svg>
    </div>
  </div>
</header>

<nav class="nav">
  <ul>
    <li>HOME</li><li>ABOUT US</li><li>SERVICES</li><li>COACHING</li><li>BLOG</li><li>SUPPORT</li><li>CONTACT US</li>
  </ul>
</nav>

<section class="hero" role="img" aria-label="Photo of a white sandy beach with a thatched parasol, palm trees and a wooden lounger by a turquoise sea">
  <div class="hero-dots"><span class="active"></span><span></span><span></span><span></span></div>
</section>

<section class="welcome">
  <h2 class="section-title">WELCOME</h2>
  <p>Sed ut perspiciatis unde omnis iste natus error sit voluptatem accusantium doloremque laudantium, totam rem aperiam, eaque ipsa quae ab illo inventore veritatis et quasi architecto beatae vitae dicta sunt explicabo.</p>
  <p>Nemo enim ipsam voluptatem quia voluptas sit aspernatur aut odit aut fugit, sed quia consequuntur magni dolores eos qui ratione voluptatem sequi nesciunt. Neque porro quisquam est, qui dolorem ipsum quia dolor sit amet, consectetur, adipisci velit, sed quia non numquam eius modi tempora incidunt ut labore et dolore magnam aliquam quaerat voluptatem.</p>
  <p>&nbsp;Ut enim ad minima veniam, quis nostrum exercitationem ullam corporis suscipit laboriosam, nisi ut aliquid ex ea commodi consequatur? Quis autem vel eum iure reprehenderit qui in ea voluptate velit esse quam nihil molestiae consequatur, vel illum qui dolorem eum fugiat quo voluptas nulla pariatur</p>
</section>

<section class="news">
  <h2 class="section-title">UPCOMING NEWS &amp; EVENTS
    <svg width="28" height="20" viewBox="0 0 28 20"><polyline points="11,3 4,10 11,17" fill="none" stroke="#333" stroke-width="3"/><polyline points="17,3 24,10 17,17" fill="none" stroke="#333" stroke-width="3"/></svg>
  </h2>
  <article class="news-item">
    <div class="news-thumb thumb-globe" role="img" aria-label="Photo of a glass globe on green grass under a blue sky"></div>
    <div><p class="news-text">Sed ut perspiciatis unde omnis iste natus error sit voluptatem accusantium doloremque laudantium, totam rem aperiam, eaque ipsa quae ab illo</p><p class="news-date">Apr 07 2014</p></div>
  </article>
  <article class="news-item">
    <div class="news-thumb thumb-island" role="img" aria-label="Photo of a small palm island in a turquoise lagoon"></div>
    <div><p class="news-text">Sed ut perspiciatis unde omnis iste natus error sit voluptatem accusantium doloremque laudantium, totam rem aperiam, eaque ipsa quae ab illo</p><p class="news-date">Apr 07 2014</p></div>
  </article>
  <article class="news-item">
    <div class="news-thumb thumb-leaf" role="img" aria-label="Photo of a butterfly on a young green sprout"></div>
    <div><p class="news-text">Sed ut perspiciatis unde omnis iste natus error sit voluptatem accusantium doloremque laudantium, totam rem aperiam, eaque ipsa quae ab</p><p class="news-date">Apr 07 2014</p></div>
  </article>
</section>

<footer class="footer">
  <div class="footer-links">Home<span>/</span>About Us<span>/</span>Services<span>/</span>Coaching<span>/</span>Blog<span>/</span>Support<span>/</span>Contact us</div>
  <div class="copyright">© 2014 company name . All Rights Reserved.</div>
  <div class="social"><span class="s1"></span><span class="s2"></span><span class="s3"></span><span class="s4"></span></div>
</footer>
</body>
</html>
```